Halvern Roofing & Waterproofing HOA & Commercial Roofing Specialists

FRONT COVER (Panel 1)
Halvern Roofing & Waterproofing
HOA & Commercial Roofing Specialists
Protecting Communities.
Preserving Property Value.
Delivering Long-Term Solutions.
📍 Serving Orange County & Surrounding Areas
INSIDE LEFT PANEL (Panel 2)
Who We Are
Halvern Roofing & Waterproofing is a trusted HOA and commercial roofing specialist serving Orange County and surrounding areas. We understand the unique needs of homeowner associations, property managers, and commercial properties—delivering reliable service, clear communication, and long-lasting results.
✔ HOA-Focused Expertise
✔ Licensed & Insured
✔ Emergency Response Available
✔ Quality Workmanship You Can Trust
INSIDE MIDDLE PANEL (Panel 3)
Roofing Services
HOA & Commercial Roofing
• Emergency roof tarping & repairs — Starting at $550
• Small & large roof repairs
• Chimney cap and spark arrestor repairs
• Preventative roof maintenance
• Roof cleaning
• Full roof replacement
We work on all roof types:
✔ Flat Roofs (Torch down, TPO, & PVC)
✔ Tile Roofs (Clay tiles, concrete tiles, and more)
✔ Shingle Roofs - KOV certified contractor
• Coating (silicone or acrylic)
No matter the size or system—we’ve got you covered.
INSIDE RIGHT PANEL (Panel 4)
Gutter Services
• Small & large gutter repairs
• Gutter cleaning & maintenance
• New gutter installation & replacement
Proper drainage protects your building—let us handle it.
BACK LEFT PANEL (Panel 5)
Deck/Balcony Waterproofing Services
• Balcony/deck maintenance
• Deck resurfacing
• Small & large deck repairs
• Full deck reconstruction
Specialized waterproofing solutions to keep decks safe, compliant, and durable.
BACK COVER (Panel 6)
Why Choose Halvern?
✔ HOA & Commercial Specialists
✔ Fully Licensed & Insured
✔ Reliable Scheduling
✔ Clear Communication
✔ Quality Materials & Craftsmanship
License Information:
C-39 Roofing Contractor
General B Contractor
License #4630257
📍 Office Location:
14 Dunmore Street, Suite J Irvine, CA 92618
📞 Contact us today for a consultation
949-372-6104 or rfp@halvernroofing.com
🌐 Serving Orange County & surrounding areas
- Gotham

```html
<!DOCTYPE html>
<html lang="en">
<head>
<meta charset="utf-8">
<title>Halvern Roofing &amp; Waterproofing – Trifold Layout</title>
<link href="https://fonts.googleapis.com/css2?family=Montserrat:wght@400;500;600;700;800&display=swap" rel="stylesheet">
<style>
  :root{
    --board:#3b3b3b;
    --brand-blue:#1e9be8;
    --brand-blue-deep:#0f78c4;
    --ink:#101010;
    --white:#ffffff;
    --sky-top:#cfe7f8;
    --sky-mid:#eef7fd;
    --pill:rgba(6,70,140,.28);
    --roof-light:#eef1f4;
    --roof-mid:#c5cbd2;
    --roof-dark:#7d838b;
    --wood:#9a6a3c;
    --wood-dark:#5a3a20;
  }
  *{box-sizing:border-box;margin:0;padding:0}
  html,body{width:806px;height:1200px;overflow:hidden}
  body{background:var(--board);font-family:"Montserrat",Arial,sans-serif;color:var(--ink);position:relative}

  .sheet-label{position:absolute;color:var(--white);font-weight:700;font-size:18px;letter-spacing:5px;text-align:center}
  .sheet-label--cover{left:118px;width:257px;top:36px}
  .sheet-label--back{left:420px;width:253px;top:36px}
  .sheet-label--outside{left:50px;width:691px;top:630px}

  .panel{position:absolute;overflow:hidden}
  .panel-art{position:absolute;inset:0;width:100%;height:100%}

  /* brand lockup */
  .brand{position:absolute;display:flex;flex-direction:column;align-items:center;line-height:1}
  .brand-name{font-weight:800;font-size:27px;letter-spacing:.5px;color:var(--ink)}
  .brand-tag{font-weight:500;font-size:8.6px;letter-spacing:.6px;margin-top:7px;color:var(--ink)}

  .service-pill{position:absolute;display:flex;align-items:center;gap:5px;background:var(--pill);color:var(--white);
    border-radius:10px;font-size:9.2px;font-weight:500;height:18px;padding:0 9px;white-space:nowrap}
  .service-pill svg{width:9px;height:11px;flex:none}

  /* ---------- cover panel ---------- */
  .cover-panel{width:257px;height:537px}
  .cover-photo{position:absolute;left:0;top:0;width:257px;height:310px;
    background:linear-gradient(125deg,var(--roof-light) 0%,#dfe3e8 35%,var(--roof-mid) 62%,var(--roof-dark) 100%)}
  .cover-panel .brand{left:12px;top:20px}
  .cover-title{position:absolute;left:0;right:0;top:322px;text-align:center;color:var(--white);font-weight:800;font-size:19.5px;line-height:1.25}
  .cover-sub{position:absolute;left:0;right:0;top:382px;text-align:center;color:var(--white);font-weight:500;font-size:10.6px}
  .values{position:absolute;left:14px;right:14px;top:408px;display:grid;grid-template-columns:repeat(3,1fr);list-style:none}
  .value{display:flex;flex-direction:column;align-items:center;text-align:center;color:var(--white);font-size:8.6px;font-weight:500;line-height:1.3;position:relative}
  .value + .value::before{content:"";position:absolute;left:0;top:0;height:82px;border-left:1px solid rgba(255,255,255,.45)}
  .value-icon{width:44px;height:44px;border-radius:50%;background:var(--ink);border:2px solid var(--white);
    box-shadow:0 0 0 1.5px #0c3a63;display:flex;align-items:center;justify-content:center;margin-bottom:6px}
  .value-icon svg{width:24px;height:24px}
  .cover-panel .service-pill{left:17px;top:497px;width:221px}

  /* ---------- back panel ---------- */
  .back-panel{width:253px;height:536px;background:linear-gradient(180deg,var(--sky-top) 0%,var(--sky-mid) 30%,#f7fbfe 50%)}
  .back-panel .brand{left:0;right:0;top:21px}
  .why-title{position:absolute;left:26px;top:104px;font-size:17.5px;font-weight:800;color:var(--ink)}
  .why-title .accent{color:var(--brand-blue)}
  .why-list{position:absolute;left:26px;top:134px;width:215px;display:grid;grid-template-columns:110px 105px;column-gap:0;list-style:none;
    font-size:8.3px;line-height:1.3;color:#222}
  .why-list li{display:flex;gap:3px;margin-bottom:0}
  .why-list .tick{width:8px;height:8px;flex:none;margin-top:1.5px}
  .why-col{list-style:none}
  .license-title{position:absolute;left:26px;top:190px;font-size:12.5px;font-weight:700}
  .license-lines{position:absolute;left:26px;top:209px;font-size:8.3px;line-height:1.33;color:#222}
  .contact-box{position:absolute;left:29px;top:369px;width:200px;height:83px;border:1.2px solid var(--white);border-radius:9px}
  .contact-phone-icon{position:absolute;left:113px;top:351px;width:31px;height:31px;border-radius:50%;background:var(--brand-blue);
    display:flex;align-items:center;justify-content:center;outline:6px solid var(--brand-blue)}
  .contact-phone-icon svg{width:31px;height:31px}
  .contact-lead{position:absolute;left:0;right:0;top:384px;text-align:center;color:var(--white);font-weight:700;font-size:14px;line-height:1.25}
  .contact-lead .big{font-size:17.5px;display:block}
  .contact-phone{position:absolute;left:0;right:0;top:428px;text-align:center;color:var(--white);font-size:11.5px;font-weight:500}
  .contact-email{position:absolute;left:50%;transform:translateX(-50%);top:444px;background:var(--brand-blue);padding:0 6px;color:var(--white);font-size:11px;font-weight:500;white-space:nowrap}
  .office-address{position:absolute;left:0;right:0;top:475px;text-align:center;color:var(--white);font-size:10px;font-weight:500}
  .back-panel .service-pill{left:19px;top:497px;width:221px}

  /* ---------- outside spread ---------- */
  .outside-spread{left:50px;top:667px;width:691px;height:488px;background:var(--brand-blue)}
  .spread-slot{position:absolute;top:0;transform-origin:0 0}
  .spread-slot--back{left:228px;transform:scale(.912)}
  .spread-slot--cover{left:459px;transform:scale(.905,.909)}

  .deck-panel{left:0;top:0;width:229px;height:488px;background:linear-gradient(180deg,var(--sky-top) 0%,var(--sky-mid) 40%,#f4f9fd 52%)}
  .deck-title{position:absolute;left:23px;top:18px;font-size:19px;font-weight:800;line-height:1.18;color:var(--ink)}
  .deck-title .accent{color:var(--brand-blue);display:block}
  .deck-rule{position:absolute;left:23px;top:71px;width:162px;height:2px;background:linear-gradient(90deg,var(--brand-blue) 50%,var(--ink) 50%)}
  .deck-grid{position:absolute;left:20px;top:90px;width:193px;height:311px;display:grid;grid-template-columns:1fr 1fr;grid-template-rows:1fr 1fr;gap:5px}
  .deck-tile{position:relative;border:1.5px solid var(--white);border-radius:7px;overflow:hidden;background:var(--ink)}
  .tile-photo{position:absolute;left:0;right:0;top:0;bottom:33px}
  .tile-photo--balcony{background:linear-gradient(180deg,#7a4c26,#b98553 55%,#8e643d)}
  .tile-photo--resurface{background:linear-gradient(160deg,#5a4a3c,#b5462f 45%,#d7c1a0 80%)}
  .tile-photo--repair{background:linear-gradient(160deg,#f2efe9,#d6b486 40%,#c59a63)}
  .tile-photo--rebuild{background:linear-gradient(160deg,#6f6a5c,#4f3b2c 50%,#7b5a3d)}
  .tile-caption{position:absolute;left:0;right:0;bottom:0;height:33px;display:flex;align-items:center;justify-content:center;text-align:center;
    color:var(--white);font-size:9.3px;font-weight:700;line-height:1.2}
  .deck-drop{position:absolute;left:98px;top:230px;width:35px;height:35px;border-radius:50%;background:var(--brand-blue);border:2px solid var(--white);
    display:flex;align-items:center;justify-content:center}
  .deck-drop svg{width:13px;height:17px}
  .deck-promise{position:absolute;left:0;right:0;top:414px;text-align:center;color:var(--white);font-size:12.5px;font-weight:700;line-height:1.3}
  .deck-checks{position:absolute;left:20px;top:450px;width:196px;height:20px;display:flex;align-items:center;justify-content:space-between;padding:0 8px 0 6px;
    background:linear-gradient(90deg,rgba(255,255,255,.0),rgba(255,255,255,.35) 30%,rgba(255,255,255,.35) 70%,rgba(255,255,255,0));
    list-style:none;font-size:8.6px;font-weight:500;color:var(--ink)}
  .deck-checks li{display:flex;align-items:center;gap:3px}
  .deck-checks svg{width:10px;height:10px}
</style>
</head>
<body>

<!-- shared symbols -->
<svg width="0" height="0" style="position:absolute" aria-hidden="true">
  <defs>
    <symbol id="icon-tick" viewBox="0 0 10 10"><circle cx="5" cy="5" r="4.3" fill="none" stroke="#1e9be8" stroke-width="1"/><path d="M3 5.1l1.4 1.4L7.1 3.8" fill="none" stroke="#1e9be8" stroke-width="1.1" stroke-linecap="round"/></symbol>
    <symbol id="icon-tick-solid" viewBox="0 0 10 10"><circle cx="5" cy="5" r="5" fill="#101010"/><path d="M2.8 5.1l1.5 1.5L7.3 3.6" fill="none" stroke="#fff" stroke-width="1.3" stroke-linecap="round"/></symbol>
    <symbol id="icon-pin" viewBox="0 0 10 12"><path d="M5 .6a4 4 0 0 0-4 4c0 3 4 6.8 4 6.8s4-3.8 4-6.8a4 4 0 0 0-4-4z" fill="none" stroke="#fff" stroke-width="1.3"/><circle cx="5" cy="4.6" r="1.4" fill="#fff"/></symbol>
    <symbol id="icon-phone" viewBox="0 0 32 32"><circle cx="16" cy="16" r="14.5" fill="none" stroke="#fff" stroke-width="1.6"/><path d="M11.5 9.5l2.6-.6 1.5 3.6-1.8 1.3a9 9 0 0 0 3.6 4.6l1.4-1.7 3.5 1.6-.7 2.7c-5.6.6-11-5.5-10.1-11.5z" fill="none" stroke="#fff" stroke-width="1.5" stroke-linejoin="round"/></symbol>
    <symbol id="icon-community" viewBox="0 0 24 24"><g fill="none" stroke="#fff" stroke-width="1.3"><circle cx="12" cy="12" r="10"/><circle cx="12" cy="9" r="2.2"/><path d="M8.3 15.5a3.7 3.7 0 0 1 7.4 0"/><circle cx="7" cy="11" r="1.6"/><circle cx="17" cy="11" r="1.6"/><path d="M4.6 16.2a2.6 2.6 0 0 1 3.6-2.1M19.4 16.2a2.6 2.6 0 0 0-3.6-2.1"/></g></symbol>
    <symbol id="icon-gear" viewBox="0 0 24 24"><g fill="none" stroke="#fff" stroke-width="1.3"><circle cx="12" cy="12" r="3"/><path d="M12 6.5v2M12 15.5v2M6.5 12h2M15.5 12h2M8.1 8.1l1.4 1.4M14.5 14.5l1.4 1.4M8.1 15.9l1.4-1.4M14.5 9.5l1.4-1.4"/><path d="M3 3h5v3H3zM16 3h5v3h-5zM3 18h5v3H3zM16 18h5v3h-5z"/></g></symbol>
    <symbol id="icon-house" viewBox="0 0 24 24"><g fill="none" stroke="#fff" stroke-width="1.3"><path d="M3 11L12 3.5 21 11"/><path d="M5 9.5V20h14V9.5"/><path d="M8 17v-2M11 17v-4M14 17v-3M17 17v-5"/><path d="M7 20.5h10"/></g></symbol>
    <symbol id="icon-drop" viewBox="0 0 12 16"><path d="M6 .5C8 4.5 11.5 7.5 11.5 10.5a5.5 5.5 0 0 1-11 0C.5 7.5 4 4.5 6 .5z" fill="#fff"/></symbol>
  </defs>
</svg>

<p class="sheet-label sheet-label--cover">COVER</p>
<p class="sheet-label sheet-label--back">BACK</p>
<p class="sheet-label sheet-label--outside">OUTSIDE PAGE</p>

<!-- ===== Cover ===== -->
<section class="panel cover-panel" style="left:118px;top:65px">
  <div class="cover-photo" role="img" aria-label="Roofer in a white hard hat fitting metal roof panels"></div>
  <svg class="panel-art" viewBox="0 0 257 537" aria-hidden="true">
    <polygon points="0,277 37,277 129,166 257,272 257,310 0,310" fill="#101010"/>
    <polygon points="0,305 47,305 129,210 211,305 257,305 257,537 0,537" fill="#1e9be8" stroke="#fff" stroke-width="3" stroke-linejoin="miter"/>
    <rect x="0" y="306" width="257" height="231" fill="#1e9be8"/>
    <g fill="#fff"><rect x="106" y="266" width="20" height="19"/><rect x="131" y="266" width="20" height="19"/><rect x="106" y="290" width="20" height="19"/><rect x="131" y="290" width="20" height="19"/></g>
  </svg>
  <div class="brand"><span class="brand-name">HALVERN</span><span class="brand-tag">ROOFING &amp; WATERPROOFING</span></div>
  <h1 class="cover-title">Halvern Roofing &amp;<br>Waterproofing</h1>
  <p class="cover-sub">HOA &amp; Commercial Roofing Specialists</p>
  <ul class="values">
    <li class="value"><span class="value-icon"><svg><use href="#icon-community"/></svg></span>Protecting<br>Communities</li>
    <li class="value"><span class="value-icon"><svg><use href="#icon-gear"/></svg></span>Delivering<br>Long-Term<br>Solutions.</li>
    <li class="value"><span class="value-icon"><svg><use href="#icon-house"/></svg></span>Preserving<br>Property Value</li>
  </ul>
  <p class="service-pill"><svg><use href="#icon-pin"/></svg>Serving Orange County &amp; Surrounding Areas</p>
</section>

<!-- ===== Back ===== -->
<section class="panel back-panel" style="left:420px;top:67px">
  <svg class="panel-art" viewBox="0 0 253 536" role="img" aria-label="Roofer carrying materials across a commercial roof, framed in a water drop">
    <defs><linearGradient id="drop-photo-back" x1="0" y1="0" x2="0" y2="1"><stop offset="0" stop-color="#4aa9e6"/><stop offset="1" stop-color="#1267a8"/></linearGradient></defs>
    <rect x="0" y="275" width="253" height="29" fill="#101010"/>
    <rect x="0" y="303" width="253" height="233" fill="#1e9be8"/>
    <path d="M178 193C200 235 230 262 230 290A52 52 0 1 1 126 290C126 262 156 235 178 193Z" fill="url(#drop-photo-back)" stroke="#fff" stroke-width="4"/>
  </svg>
  <div class="brand"><span class="brand-name">HALVERN</span><span class="brand-tag">ROOFING &amp; WATERPROOFING</span></div>
  <h2 class="why-title">Why Choose <span class="accent">Halvern?</span></h2>
  <div class="why-list">
    <ul class="why-col">
      <li><svg class="tick"><use href="#icon-tick"/></svg><span>HOA &amp; Commercial Specialists</span></li>
      <li><svg class="tick"><use href="#icon-tick"/></svg><span>Fully Licensed &amp; Insured</span></li>
      <li><svg class="tick"><use href="#icon-tick"/></svg><span>Reliable Scheduling</span></li>
    </ul>
    <ul class="why-col">
      <li><svg class="tick"><use href="#icon-tick"/></svg><span>Clear Communication</span></li>
      <li><svg class="tick"><use href="#icon-tick"/></svg><span>Quality Materials &amp; Craftsmanship</span></li>
    </ul>
  </div>
  <h3 class="license-title">License Information</h3>
  <p class="license-lines">C-39 Roofing Contractor<br>General B Contractor<br>License #4630257</p>
  <div class="contact-box"></div>
  <span class="contact-phone-icon"><svg><use href="#icon-phone"/></svg></span>
  <p class="contact-lead">Contact us today<span class="big">for a consultation</span></p>
  <p class="contact-phone">949-372-6104</p>
  <p class="contact-email">or rfp@halvernroofing.com</p>
  <p class="office-address">14 Dunmore Street, Suite J Irvine, CA 92618</p>
  <p class="service-pill"><svg><use href="#icon-pin"/></svg>Serving Orange County &amp; Surrounding Areas</p>
</section>

<!-- ===== Outside spread ===== -->
<section class="panel outside-spread">

  <div class="panel deck-panel">
    <svg class="panel-art" viewBox="0 0 229 488" aria-hidden="true">
      <rect x="0" y="251" width="229" height="29" fill="#101010"/>
      <rect x="0" y="279" width="229" height="209" fill="#1e9be8"/>
    </svg>
    <h2 class="deck-title">Deck &amp; Balcony<span class="accent">Services</span></h2>
    <div class="deck-rule"></div>
    <div class="deck-grid">
      <figure class="deck-tile"><div class="tile-photo tile-photo--balcony" role="img" aria-label="Wooden balcony with railings"></div><figcaption class="tile-caption">Balcony &amp; deck<br>maintenance</figcaption></figure>
      <figure class="deck-tile"><div class="tile-photo tile-photo--resurface" role="img" aria-label="Sander resurfacing deck boards"></div><figcaption class="tile-caption">Deck resurfacing</figcaption></figure>
      <figure class="deck-tile"><div class="tile-photo tile-photo--repair" role="img" aria-label="Hammer fixing new deck boards"></div><figcaption class="tile-caption">Small &amp; large<br>deck repairs</figcaption></figure>
      <figure class="deck-tile"><div class="tile-photo tile-photo--rebuild" role="img" aria-label="Worker rebuilding a deck frame"></div><figcaption class="tile-caption">Full deck<br>reconstruction</figcaption></figure>
    </div>
    <span class="deck-drop"><svg><use href="#icon-drop"/></svg></span>
    <p class="deck-promise">Specialized waterproofing<br>solutions to keep</p>
    <ul class="deck-checks">
      <li><svg><use href="#icon-tick-solid"/></svg>Decks safe</li>
      <li><svg><use href="#icon-tick-solid"/></svg>Compliant</li>
      <li><svg><use href="#icon-tick-solid"/></svg>Durable</li>
    </ul>
  </div>

  <div class="spread-slot spread-slot--back">
    <section class="panel back-panel" style="left:0;top:0">
      <svg class="panel-art" viewBox="0 0 253 536" role="img" aria-label="Roofer carrying materials across a commercial roof, framed in a water drop">
        <defs><linearGradient id="drop-photo-spread" x1="0" y1="0" x2="0" y2="1"><stop offset="0" stop-color="#4aa9e6"/><stop offset="1" stop-color="#1267a8"/></linearGradient></defs>
        <rect x="0" y="275" width="253" height="29" fill="#101010"/>
        <rect x="0" y="303" width="253" height="233" fill="#1e9be8"/>
        <path d="M178 193C200 235 230 262 230 290A52 52 0 1 1 126 290C126 262 156 235 178 193Z" fill="url(#drop-photo-spread)" stroke="#fff" stroke-width="4"/>
      </svg>
      <div class="brand"><span class="brand-name">HALVERN</span><span class="brand-tag">ROOFING &amp; WATERPROOFING</span></div>
      <h2 class="why-title">Why Choose <span class="accent">Halvern?</span></h2>
      <div class="why-list">
        <ul class="why-col">
          <li><svg class="tick"><use href="#icon-tick"/></svg><span>HOA &amp; Commercial Specialists</span></li>
          <li><svg class="tick"><use href="#icon-tick"/></svg><span>Fully Licensed &amp; Insured</span></li>
          <li><svg class="tick"><use href="#icon-tick"/></svg><span>Reliable Scheduling</span></li>
        </ul>
        <ul class="why-col">
          <li><svg class="tick"><use href="#icon-tick"/></svg><span>Clear Communication</span></li>
          <li><svg class="tick"><use href="#icon-tick"/></svg><span>Quality Materials &amp; Craftsmanship</span></li>
        </ul>
      </div>
      <h3 class="license-title">License Information</h3>
      <p class="license-lines">C-39 Roofing Contractor<br>General B Contractor<br>License #4630257</p>
      <div class="contact-box"></div>
      <span class="contact-phone-icon"><svg><use href="#icon-phone"/></svg></span>
      <p class="contact-lead">Contact us today<span class="big">for a consultation</span></p>
      <p class="contact-phone">949-372-6104</p>
      <p class="contact-email">or rfp@halvernroofing.com</p>
      <p class="office-address">14 Dunmore Street, Suite J Irvine, CA 92618</p>
      <p class="service-pill"><svg><use href="#icon-pin"/></svg>Serving Orange County &amp; Surrounding Areas</p>
    </section>
  </div>

  <div class="spread-slot spread-slot--cover">
    <section class="panel cover-panel" style="left:0;top:0">
      <div class="cover-photo" role="img" aria-label="Roofer in a white hard hat fitting metal roof panels"></div>
      <svg class="panel-art" viewBox="0 0 257 537" aria-hidden="true">
        <polygon points="0,277 37,277 129,166 257,272 257,310 0,310" fill="#101010"/>
        <polygon points="0,305 47,305 129,210 211,305 257,305 257,537 0,537" fill="#1e9be8" stroke="#fff" stroke-width="3"/>
        <rect x="0" y="306" width="257" height="231" fill="#1e9be8"/>
        <g fill="#fff"><rect x="106" y="266" width="20" height="19"/><rect x="131" y="266" width="20" height="19"/><rect x="106" y="290" width="20" height="19"/><rect x="131" y="290" width="20" height="19"/></g>
      </svg>
      <div class="brand"><span class="brand-name">HALVERN</span><span class="brand-tag">ROOFING &amp; WATERPROOFING</span></div>
      <h2 class="cover-title">Halvern Roofing &amp;<br>Waterproofing</h2>
      <p class="cover-sub">HOA &amp; Commercial Roofing Specialists</p>
      <ul class="values">
        <li class="value"><span class="value-icon"><svg><use href="#icon-community"/></svg></span>Protecting<br>Communities</li>
        <li class="value"><span class="value-icon"><svg><use href="#icon-gear"/></svg></span>Delivering<br>Long-Term<br>Solutions.</li>
        <li class="value"><span class="value-icon"><svg><use href="#icon-house"/></svg></span>Preserving<br>Property Value</li>
      </ul>
      <p class="service-pill"><svg><use href="#icon-pin"/></svg>Serving Orange County &amp; Surrounding Areas</p>
    </section>
  </div>

</section>
</body>
</html>
```